Business Card Design Project - del varosi group

dear Sirs

we need business card design for our group ( DEL Varosi Group ) , i have got the Logo design of our group from pixel harbor in previous , so all need details relating to our group i think available with you, as well as the the chosen logo design

we hope to provide us with business card logo that to be appropaite and satisfactory to us .

thanks

note : logo design of our group is attached .
Updates

Reason: please extend the deadline of my project for additional 15 days because i didn't received appropriate design for our gruop yet . kindly beaware that i have received 77 design till now , supossed to send me 200-250 design at least . thanks

Target Market(s)

contents

name : Kerem EL Nadiri

position : Operation Manager

Industry/Entity Type

Business

Requirements
Must have

• person name

group logo
Nice to have
• logo color matching with back background

```html
<!DOCTYPE html>
<html lang="en">
<head>
<meta charset="utf-8">
<title>Kerem EL Nadiri – DEL Varosi Group Business Card</title>
<link rel="stylesheet" href="https://fonts.googleapis.com/css2?family=Arimo:ital,wght@0,700;1,700&family=Roboto+Condensed:wght@700&display=swap">
<style>
  :root {
    --card-blue: #0435c8;
    --frame-white: #ffffff;
    --name-gold: #c6960c;
    --title-yellow: #f2da62;
    --value-gold: #c9980f;
    --label-white: #ffffff;
    --swoosh-light: #f3e78e;
    --swoosh-deep: #c08f06;
  }
  * { margin: 0; padding: 0; box-sizing: border-box; }
  html, body { width: 1200px; height: 686px; overflow: hidden; background: var(--card-blue); }
  .card {
    position: relative;
    width: 1200px;
    height: 686px;
    background: var(--card-blue);
    overflow: hidden;
    font-family: "Arimo", Arial, sans-serif;
  }
  .frame-bar { position: absolute; background: var(--frame-white); }
  .frame-top    { left: 69px;  top: 41px;  width: 388px; height: 19px; }
  .frame-left   { left: 69px;  top: 41px;  width: 15px;  height: 362px; }
  .frame-right  { left: 441px; top: 41px;  width: 16px;  height: 140px; }
  .frame-bottom { left: 69px;  top: 386px; width: 370px; height: 17px; }

  .person-name {
    position: absolute; left: 110px; top: 88px;
    font-weight: 700; font-size: 33px; letter-spacing: 0.5px;
    color: var(--name-gold); text-transform: uppercase; white-space: nowrap;
  }
  .person-title {
    position: absolute; left: 108px; top: 132px;
    font-weight: 700; font-style: italic; font-size: 25.5px; letter-spacing: 0.4px;
    color: var(--title-yellow); text-transform: uppercase; white-space: nowrap;
  }
  .contact-list { position: absolute; left: 91px; top: 207px; list-style: none; }
  .contact-row { display: flex; align-items: baseline; height: 28.7px; white-space: nowrap; }
  .contact-label {
    width: 82px; font-weight: 700; font-size: 17px;
    font-variant: small-caps; color: var(--label-white);
  }
  .contact-value {
    font-family: "Roboto Condensed", "Arial Narrow", sans-serif;
    font-weight: 700; font-size: 17px; color: var(--value-gold); letter-spacing: 0.3px;
  }
  .contact-value.is-small { font-size: 13px; text-transform: uppercase; letter-spacing: 0.6px; }

  .brand-decoration { position: absolute; left: 470px; top: 0; width: 730px; height: 686px; }

  .brand-name {
    position: absolute; left: 70px; top: 540px;
    font-weight: 700; font-size: 50px; letter-spacing: 1px;
    color: var(--frame-white); white-space: nowrap; text-transform: uppercase;
  }
</style>
</head>
<body>
<main class="card">
  <div class="frame-bar frame-top"></div>
  <div class="frame-bar frame-left"></div>
  <div class="frame-bar frame-right"></div>
  <div class="frame-bar frame-bottom"></div>

  <h1 class="person-name">Kerem EL Nadiri</h1>
  <p class="person-title">Operation Manager</p>

  <ul class="contact-list">
    <li class="contact-row"><span class="contact-label">Tel :</span><span class="contact-value">01234-56789-01234</span></li>
    <li class="contact-row"><span class="contact-label">Fax :</span><span class="contact-value">01234-56789-01234</span></li>
    <li class="contact-row"><span class="contact-label">Mobile :</span><span class="contact-value">01234-56789-01234</span></li>
    <li class="contact-row"><span class="contact-label">Email :</span><span class="contact-value is-small">knadiri@delvarosigroup.com</span></li>
    <li class="contact-row"><span class="contact-label">Website :</span><span class="contact-value is-small">www.delvarosigroup.com</span></li>
    <li class="contact-row"><span class="contact-label">PO . Box :</span><span class="contact-value"></span></li>
  </ul>

  <svg class="brand-decoration" role="img" aria-label="Large decorative brand symbol in pale to deep gold tones" viewBox="0 0 730 686" xmlns="http://www.w3.org/2000/svg">
    <defs>
      <radialGradient id="decorGlow" cx="62%" cy="58%" r="60%">
        <stop offset="0%" stop-color="var(--swoosh-light)" stop-opacity="0.55"/>
        <stop offset="55%" stop-color="var(--swoosh-deep)" stop-opacity="0.3"/>
        <stop offset="100%" stop-color="var(--card-blue)" stop-opacity="0"/>
      </radialGradient>
    </defs>
    <rect width="730" height="686" fill="url(#decorGlow)"/>
  </svg>

  <p class="brand-name">DEL Varosi Group</p>
</main>
</body>
</html>
```